Refresh of far from plain IT company website

Our web site is starting to show it's age. You can see the existing site here: www.plumbwick.net. As a growing company we want to come across as a dynamic collection of IT experts.

We want to update the design so are open to any colour palette and look, but want to retain our current table logo. We use the logo on our business cards but with a white background - see the attached file, so you don't need to keep the brown or the green.

The design should consider the range of browsers that will be looking at the site - so please show how it will look on a wide screen laptop and a 768x1024 tablet.

We want to add some pages about our team and their skills, probably with photos of each person on the team.

This is an uncoded project - the PSD files of the design is required, not coding.
Updates

Thanks everyone for the submissions so far.  It's a holiday day in the UK today but we will get some feedback on the designs so far out to you.

Target Market(s)

Architects and other creative types looking for IT support

Industry/Entity Type

Business

Font styles to use
Serif
Sans Serif

Requirements
Must have
• Must look good on a laptop and an iPad.

```html
<!DOCTYPE html>
<html lang="en">
<head>
<meta charset="utf-8">
<title>plumbwick — IT support for business</title>
<link href="https://fonts.googleapis.com/css2?family=Ubuntu:ital,wght@0,400;0,500;0,700;1,700&family=Open+Sans:wght@400;600&display=swap" rel="stylesheet">
<style>
:root{
  --plum:#8c0b4f;
  --plum-dark:#6e0a3e;
  --gold:#d4a50c;
  --ink:#333333;
  --muted:#666666;
  --rule:#dddddd;
  --panel:#efefef;
  --footer:#333333;
  --white:#ffffff;
}
*{box-sizing:border-box;margin:0;padding:0}
html,body{width:1034px;height:1200px;overflow:hidden;background:var(--white)}
body{position:relative;font-family:"Open Sans",Arial,sans-serif;color:var(--ink)}
.abs{position:absolute}
.top-rule{left:0;top:0;width:1034px;height:3px;background:var(--plum)}

/* header */
.brand{left:198px;top:26px;display:flex;align-items:center;gap:14px}
.brand-mark{width:26px;height:26px;background:var(--gold)}
.brand-name{font-family:"Ubuntu",sans-serif;font-weight:500;font-size:42px;color:var(--plum);line-height:1}
.call{right:191px;top:17px;font-family:"Ubuntu",sans-serif;font-size:14px;color:#555;letter-spacing:.3px}
.social{right:191px;top:54px;display:flex;gap:8px}
.social span{width:27px;height:27px;border-radius:50%;background:#e6e6e6;box-shadow:0 1px 2px rgba(0,0,0,.25)}
.social span.on{background:#1b95d1}
.nav{left:198px;top:96px;display:flex;font-family:"Ubuntu",sans-serif;font-size:10px;text-transform:uppercase;color:#444}
.nav a{color:inherit;text-decoration:none;padding:3px 0 8px;position:relative}
.nav .sep{width:1px;height:12px;background:#bbb;margin:2px 19px 0}
.nav a.active{color:var(--plum);font-weight:700;border-bottom:2px solid var(--plum)}
.nav a.active::after{content:"";position:absolute;left:50%;bottom:-6px;margin-left:-4px;border:4px solid transparent;border-top-color:var(--plum)}

/* hero */
.hero{left:0;top:123px;width:1034px;height:331px;background:linear-gradient(100deg,#9fb7c6 0%,#cfdde6 35%,#e9eef1 55%,#c3d5df 75%,#a9c2d0 100%)}
.hero-caption{left:196px;top:375px;font-family:"Ubuntu",sans-serif;font-size:21px;color:var(--plum)}
.dots{left:776px;top:385px;display:flex;gap:7px}
.dots i{width:11px;height:11px;border-radius:50%;background:#d5d9dc;border:2px solid #fff}
.dots i.on{background:var(--plum)}
.hero-band{left:0;top:452px;width:1034px;height:3px;background:var(--plum)}
.services-bg{left:0;top:455px;width:1034px;height:55px;background:linear-gradient(#f1f1f1,#fff)}
.service{top:424px;width:140px;margin-left:-70px;text-align:center}
.service .disc{width:52px;height:52px;margin:0 auto;border-radius:50%;background:#4b4b4b;border:3px solid #fff;box-shadow:0 2px 3px rgba(0,0,0,.35);display:flex;align-items:center;justify-content:center}
.service.active .disc{background:var(--plum);box-shadow:0 3px 0 var(--gold),0 2px 4px rgba(0,0,0,.3)}
.service p{margin-top:12px;font-size:10.5px;font-weight:600;color:#222}

/* sections */
.heading{font-family:"Ubuntu",sans-serif;font-weight:700;font-style:italic;font-size:17px;color:var(--plum);padding:0 0 4px 2px;border-bottom:1px solid var(--rule)}
.about{left:198px;top:532px;width:414px}
.about p{font-size:10.5px;line-height:18px;color:#333;margin-top:11px}
.about p+p{margin-top:13px}
.more{display:block;text-align:right;margin-top:9px;font-family:"Ubuntu",sans-serif;font-size:11px;color:var(--gold)}
.team{left:642px;top:528px;width:193px;height:193px;border-radius:50%;border:3px solid var(--plum);overflow:hidden;box-shadow:0 6px 8px rgba(0,0,0,.15)}
.team .photo{position:absolute;inset:0;background:linear-gradient(#f4f4f4 0%,#c7d2e0 50%,#8ea3c1 100%)}
.team .band{position:absolute;left:0;right:0;top:132px;height:70px;background:var(--plum);color:#fff;font-family:"Ubuntu",sans-serif;font-weight:500;font-size:20px;text-align:center;padding-top:9px}

.col-head{top:756px;width:310px}
.card{top:793px;width:310px;height:224px;background:var(--panel);border:1px solid #cfcfcf;box-shadow:0 0 0 4px #fafafa inset,0 6px 6px -3px rgba(0,0,0,.25)}
.quote{position:absolute;left:0;width:100%;display:flex;padding:0 10px}
.person{width:100px;text-align:center;padding-top:12px}
.avatar{width:60px;height:60px;margin:0 auto;border-radius:50%;background:linear-gradient(#d9d9d9,#8a8f96);border:3px solid #fff;box-shadow:0 1px 3px rgba(0,0,0,.3)}
.person b{display:block;margin-top:7px;font-family:"Ubuntu",sans-serif;font-weight:500;font-size:12px;color:#222}
.person small{display:block;font-size:9px;color:#666}
.quote blockquote{flex:1;border-left:1px solid #ddd;padding:14px 0 0 26px;position:relative;font-size:9px;line-height:13.6px;color:#333}
.quote blockquote::before{content:"\201C";position:absolute;left:10px;top:4px;font-size:22px;color:#888;font-family:Georgia,serif}
.divider{position:absolute;left:100px;right:10px;border-top:1px solid #ddd}
.news-item{position:absolute;left:22px;right:22px;display:flex;gap:16px}
.news-item .date{font-size:10px;font-weight:600;color:var(--plum)}
.news-item p{font-size:9.6px;line-height:13.6px;color:#333;margin-top:4px}
.pager{top:1022px;display:flex;gap:6px}
.pager span{width:15px;height:15px;border-radius:50%;border:1px solid #555;display:flex;align-items:center;justify-content:center}

/* footer */
.footer{left:0;top:1058px;width:1034px;height:120px;background:var(--footer);color:#fff}
.footer h4{position:absolute;top:11px;font-family:"Ubuntu",sans-serif;font-weight:400;font-size:13px}
.links{position:absolute;top:43px;list-style:none;font-size:8.5px;text-transform:uppercase}
.links li{height:18.2px;padding-left:11px;position:relative}
.links li::before{content:"›";position:absolute;left:0;top:-3px;color:var(--gold);font-size:11px}
.vline{position:absolute;top:50px;width:1px;height:60px;background:#4a4a4a}
.nl-text{position:absolute;left:430px;top:40px;font-size:9.2px;line-height:11px}
.nl-input{position:absolute;left:429px;top:66px;width:114px;height:17px;background:#fff;color:#888;font-size:7.5px;padding:3px 6px;border-radius:2px}
.nl-btn{position:absolute;left:429px;top:90px;width:52px;height:17px;background:var(--plum);border:1px solid #ccc;font-size:9px;font-weight:600;text-align:center;line-height:15px}
.map{position:absolute;left:635px;top:41px;width:81px;height:62px;background:#d8d8d2}
.contact{position:absolute;left:730px;font-size:8.8px;line-height:11px;display:flex;gap:8px}
.contact svg{flex:none;margin-top:1px}
.copy{left:0;top:1178px;width:1034px;height:22px;background:var(--plum);color:#fff;font-family:"Ubuntu",sans-serif;font-size:10.5px;text-align:center;line-height:22px}
</style>
</head>
<body>
<div class="abs top-rule"></div>

<header>
  <div class="abs brand"><span class="brand-mark"></span><span class="brand-name">plumbwick</span></div>
  <div class="abs call">CALL US: 020 7946 0381</div>
  <div class="abs social" aria-label="Social profiles"><span class="on"></span><span></span><span></span><span></span></div>
  <nav class="abs nav">
    <a class="active">Home</a><span class="sep"></span>
    <a>About Us</a><span class="sep"></span>
    <a>What We Do</a><span class="sep"></span>
    <a>News Blog</a><span class="sep"></span>
    <a>Articles</a><span class="sep"></span>
    <a>Clients</a><span class="sep"></span>
    <a>Partners</a><span class="sep"></span>
    <a>Contact Us</a>
  </nav>
</header>

<section>
  <div class="abs hero" role="img" aria-label="Woman in safety glasses touching a translucent interface screen"></div>
  <div class="abs hero-caption">Serious IT support for business</div>
  <div class="abs dots"><i class="on"></i><i></i><i></i><i></i></div>
  <div class="abs services-bg"></div>
  <div class="abs hero-band"></div>

  <div class="abs service" style="left:258px"><div class="disc"><svg width="26" height="26" viewBox="0 0 26 26"><path d="M5 21 L15 11" stroke="#fff" stroke-width="4" stroke-linecap="round"/><circle cx="17" cy="9" r="5" fill="#fff"/><circle cx="19" cy="7" r="2.2" fill="#4b4b4b"/></svg></div><p>It Support &amp; Management</p></div>
  <div class="abs service" style="left:390px"><div class="disc"><svg width="30" height="22" viewBox="0 0 30 22"><path d="M7 19 a5 5 0 0 1 0-10 a7 7 0 0 1 13-2 a6 6 0 0 1 3 12 z" fill="none" stroke="#fff" stroke-width="2.4"/></svg></div><p>Cloud Computing</p></div>
  <div class="abs service active" style="left:519px"><div class="disc"><svg width="20" height="28" viewBox="0 0 20 28"><path d="M10 1 C14 6 16 8 14 12 H6 C4 8 7 6 10 1Z" fill="#fff"/><rect x="5" y="13" width="10" height="14" rx="1" fill="#fff"/><rect x="7" y="16" width="6" height="2" fill="#8c0b4f"/></svg></div><p>Disaster Recovery</p></div>
  <div class="abs service" style="left:650px"><div class="disc"><svg width="20" height="28" viewBox="0 0 20 28"><rect x="6" y="2" width="8" height="17" fill="#fff"/><path d="M7 6h6M7 10h6M7 14h6" stroke="#4b4b4b"/><path d="M10 19v5M3 25h14" stroke="#fff" stroke-width="2"/></svg></div><p>Virtualisation</p></div>
  <div class="abs service" style="left:774px"><div class="disc"><svg width="28" height="26" viewBox="0 0 28 26"><path d="M14 3 L25 23 H3 Z" fill="none" stroke="#fff" stroke-width="3"/><path d="M6 17 H22" stroke="#fff" stroke-width="2.5"/></svg></div><p>CAD Services</p></div>
</section>

<section class="abs about">
  <h2 class="heading">ABOUT US</h2>
  <p>Lorem ipsum dolor sit amet, consectetuer adipiscing elit, sed diam nonummy nibh euismod tincidunt ut laoreet dolore magna aliquam erat volutpat. Ut wisi enim ad minim veniam, quis nostrud exerci tation ullamcorper suscipit lobortis nisl ut aliquip ex ea comsed diam nonummy nibh euism od tincidunt ut laoreet dolore magna aliquam erat volutpat.</p>
  <p>Lorem ipsum dolor sit amet, consectetuer adipiscing elit, sed diam nonummy nibh euismod tincidunt ut laoreet dolore magna aliquam erat volutpat. Ut wisi enim ad minim veniam, quis nostrud....</p>
  <a class="more">READ MORE...</a>
</section>
<div class="abs team">
  <div class="photo" role="img" aria-label="Group photo of the support team"></div>
  <div class="band">OUR TEAM</div>
</div>

<h2 class="abs heading col-head" style="left:198px">TESTIMONIALS</h2>
<div class="abs card" style="left:198px">
  <div class="quote" style="top:0">
    <div class="person"><div class="avatar" role="img" aria-label="Portrait of client"></div><b>Daniel Orrey</b><small>Businessman</small></div>
    <blockquote>Lorem ipsum dolor sit amet, consectetuer adipiscing elit, sed diam nonummy nibh euismod tincidunt ut laoreet dolore magna aliquam erat volutpat. Ut wisi enim ad minim. ”</blockquote>
  </div>
  <div class="divider" style="top:112px"></div>
  <div class="quote" style="top:110px">
    <div class="person"><div class="avatar" role="img" aria-label="Portrait of client"></div><b>Daniel Orrey</b><small>Businessman</small></div>
    <blockquote>Lorem ipsum dolor sit amet, consectetuer adipiscing elit, sed diam nonummy nibh euismod tincidunt ut laoreet dolore magna aliquam erat volutpat. Ut wisi enim ad minim. ”</blockquote>
  </div>
</div>
<div class="abs pager" style="left:327px"><span><svg width="9" height="7"><path d="M8 3.5H1M4 .5 1 3.5 4 6.5" fill="none" stroke="#555"/></svg></span><span><svg width="9" height="7"><path d="M1 3.5H8M5 .5 8 3.5 5 6.5" fill="none" stroke="#555"/></svg></span></div>

<h2 class="abs heading col-head" style="left:534px">LATEST NEWS</h2>
<div class="abs card" style="left:534px">
  <div class="news-item" style="top:16px"><svg width="30" height="30" viewBox="0 0 30 30"><rect x="2" y="4" width="26" height="24" rx="3" fill="none" stroke="#555" stroke-width="2.4"/><path d="M2 10h26M9 1v6M21 1v6" stroke="#555" stroke-width="2.4"/><g fill="#555"><rect x="6" y="13" width="4" height="3"/><rect x="13" y="13" width="4" height="3"/><rect x="20" y="13" width="4" height="3"/><rect x="6" y="19" width="4" height="3"/><rect x="13" y="19" width="4" height="3"/><rect x="20" y="19" width="4" height="3"/></g></svg><div><div class="date">12-APR-2014</div><p>Lorem ipsum dolor sit amet, consectetuer adipiscil ng elit, sed diam nonummy nibh...</p></div></div>
  <div class="divider" style="left:22px;top:74px"></div>
  <div class="news-item" style="top:91px"><svg width="30" height="30" viewBox="0 0 30 30"><rect x="2" y="4" width="26" height="24" rx="3" fill="none" stroke="#555" stroke-width="2.4"/><path d="M2 10h26M9 1v6M21 1v6" stroke="#555" stroke-width="2.4"/><g fill="#555"><rect x="6" y="13" width="4" height="3"/><rect x="13" y="13" width="4" height="3"/><rect x="20" y="13" width="4" height="3"/><rect x="6" y="19" width="4" height="3"/><rect x="13" y="19" width="4" height="3"/><rect x="20" y="19" width="4" height="3"/></g></svg><div><div class="date">15-APR-2014</div><p>Lorem ipsum dolor sit amet, consectetuer adipiscil ng elit, sed diam nonummy nibh...</p></div></div>
  <div class="divider" style="left:22px;top:149px"></div>
  <div class="news-item" style="top:166px"><svg width="30" height="30" viewBox="0 0 30 30"><rect x="2" y="4" width="26" height="24" rx="3" fill="none" stroke="#555" stroke-width="2.4"/><path d="M2 10h26M9 1v6M21 1v6" stroke="#555" stroke-width="2.4"/><g fill="#555"><rect x="6" y="13" width="4" height="3"/><rect x="13" y="13" width="4" height="3"/><rect x="20" y="13" width="4" height="3"/><rect x="6" y="19" width="4" height="3"/><rect x="13" y="19" width="4" height="3"/><rect x="20" y="19" width="4" height="3"/></g></svg><div><div class="date">17-APR-2014</div><p>Lorem ipsum dolor sit amet, consectetuer adipiscil ng elit, sed diam nonummy nibh...</p></div></div>
</div>
<div class="abs pager" style="left:671px"><span><svg width="9" height="7"><path d="M8 3.5H1M4 .5 1 3.5 4 6.5" fill="none" stroke="#555"/></svg></span><span><svg width="9" height="7"><path d="M1 3.5H8M5 .5 8 3.5 5 6.5" fill="none" stroke="#555"/></svg></span></div>

<footer class="abs footer">
  <h4 style="left:198px">Quick Links</h4>
  <ul class="links" style="left:198px"><li>Home</li><li>About Us</li><li>What We Do</li><li>News Blog</li></ul>
  <ul class="links" style="left:283px"><li>Articles</li><li>Clients</li><li>Partners</li><li>Contact Us</li></ul>
  <div class="vline" style="left:388px"></div>
  <h4 style="left:430px">Newsletter Signup</h4>
  <p class="nl-text">Lorem ipsum dolor sit amet,<br>consectetuer adipiscing elit.</p>
  <div class="nl-input">Enter your email address</div>
  <div class="nl-btn">SUBMIT</div>
  <div class="vline" style="left:593px"></div>
  <h4 style="left:635px">Contact Info</h4>
  <div class="map" role="img" aria-label="Street map showing office location"></div>
  <div class="contact" style="top:44px"><svg width="9" height="12" viewBox="0 0 9 12"><path d="M4.5 12 C1 7 0 5.5 0 4.5a4.5 4.5 0 0 1 9 0C9 5.5 8 7 4.5 12Z" fill="#d4a50c"/><circle cx="4.5" cy="4.5" r="1.6" fill="#333"/></svg><span>Lorem ipsum dolor sit<br>amet, consectetuer<br>adipiscing elit.</span></div>
  <div class="contact" style="top:86px"><svg width="10" height="10" viewBox="0 0 10 10"><circle cx="5" cy="5" r="4.3" fill="none" stroke="#d4a50c" stroke-width="1.2"/><path d="M3.5 3c0 2 1.5 3.5 3.5 3.5" stroke="#d4a50c" stroke-width="1.2" fill="none"/></svg><span>020 7946 0381</span></div>
  <div class="contact" style="top:102px"><svg width="10" height="8" viewBox="0 0 10 8"><rect width="10" height="8" fill="#d4a50c"/><path d="M0 0 5 4.5 10 0" stroke="#333" fill="none"/></svg><span>website@plumbwick.net</span></div>
</footer>
<div class="abs copy">© 2014 plumbwick. All Rights Reserved.</div>
</body>
</html>
```